Business Card

THIS IS THE CARD INFORMATION
DEVELOPMENT I FINANCING I PROPERTY MANAGEMENT
DANIEL OKAFOR
3182 SW 74th Terrace
Coral Springs, FL 33076
Telephone I 855.437.2618
Facsimile I 855.437.2675
Industry/Entity Type
Business

```html
<!DOCTYPE html>
<html lang="en">
<head>
<meta charset="utf-8">
<title>Meridian Hale &amp; Company — Business Card</title>
<link rel="stylesheet" href="https://fonts.googleapis.com/css2?family=Montserrat:wght@700&family=Nunito+Sans:wght@400;600&display=swap">
<style>
  :root {
    --backdrop: #26002a;
    --card: #ffffff;
    --ink: #2b2b2b;
    --accent: #a4268f;
    --wash-pink: #f4e8f1;
    --wash-mauve: #e2c6dc;
    --wash-grey: #f4f3f4;
    --wash-grey-mid: #e8e1e8;
  }
  html, body {
    margin: 0;
    width: 1200px;
    height: 1000px;
    overflow: hidden;
    background: var(--backdrop);
  }
  .card {
    position: absolute;
    left: 109px;
    top: 202px;
    width: 978px;
    height: 576px;
    background: var(--card);
    overflow: hidden;
  }
  .card__backdrop {
    position: absolute;
    inset: 0;
  }
  .brand {
    position: absolute;
    left: 172px;
    top: 92px;
    display: flex;
    align-items: center;
    gap: 22px;
  }
  .brand__dot {
    width: 118px;
    height: 118px;
    border-radius: 50%;
    background: var(--accent);
    flex: none;
  }
  .brand__name {
    font-family: "Montserrat", sans-serif;
    font-weight: 700;
    color: var(--ink);
    line-height: 1;
    margin: 0;
  }
  .brand__line {
    display: block;
    font-size: 58px;
    letter-spacing: -1px;
  }
  .brand__line--sub {
    font-size: 30px;
    text-align: right;
    margin-top: 6px;
    letter-spacing: 0;
  }
  .services {
    position: absolute;
    left: 297px;
    top: 232px;
    margin: 0;
    font-family: "Nunito Sans", sans-serif;
    font-weight: 600;
    font-size: 17px;
    letter-spacing: 1.5px;
    color: var(--accent);
  }
  .contact {
    position: absolute;
    left: 297px;
    top: 278px;
    margin: 0;
    display: grid;
    grid-template-columns: 122px auto;
    row-gap: 6px;
    font-family: "Nunito Sans", sans-serif;
    font-size: 21px;
    line-height: 27px;
  }
  .contact dt { color: var(--ink); margin: 0; }
  .contact dd { color: var(--accent); margin: 0; }
  .contact__holder { color: var(--ink); font-weight: 600; }
</style>
</head>
<body>
  <section class="card">
    <svg class="card__backdrop" width="978" height="576" viewBox="0 0 978 576" aria-hidden="true">
      <defs>
        <linearGradient id="tower-fill" x1="0" y1="0" x2="1" y2="0">
          <stop offset="0" stop-color="#c05fb3"/>
          <stop offset="1" stop-color="#9c4b93"/>
        </linearGradient>
      </defs>
      <polygon points="0,0 0,576 520,576" fill="var(--wash-pink)"/>
      <polygon points="0,576 600,230 716,576" fill="var(--wash-grey)"/>
      <polygon points="0,576 520,576 400,440" fill="var(--wash-grey-mid)" opacity="0.8"/>
      <polygon points="0,278 0,576 296,576" fill="var(--wash-mauve)"/>
      <polygon points="650,230 978,300 978,240" fill="var(--wash-grey)" opacity="0.7"/>
      <rect class="card__skyline" x="53" y="364" width="168" height="212" fill="url(#tower-fill)" opacity="0.85" role="img" aria-label="Illustration of stylised city towers"/>
    </svg>

    <div class="brand">
      <span class="brand__dot"></span>
      <h1 class="brand__name">
        <span class="brand__line">MERIDIAN HALE</span>
        <span class="brand__line brand__line--sub">&amp; COMPANY</span>
      </h1>
    </div>

    <p class="services">DEVELOPMENT | FINANCING | PROPERTY MANAGEMENT</p>

    <dl class="contact">
      <dt>NAME:</dt><dd class="contact__holder">DANIEL OKAFOR</dd>
      <dt>ADDRESS:</dt><dd>3182 SW 74th Terrace<br>Coral Springs, FL 33076</dd>
      <dt>PHONE:</dt><dd>855.437.2618</dd>
      <dt>FAX:</dt><dd>855.437.2675</dd>
      <dt>WEB:</dt><dd>WWW.MERIDIANHALE.COM</dd>
      <dt>EMAIL:</dt><dd>CONTACT@MERIDIANHALE.COM</dd>
    </dl>
  </section>
</body>
</html>
```